Slider images for online fax service homepage

QuilNet® needs 4 slider images for our newly designed homepage. The slider images should convey professionalism and simplicity without feeling cold or stuffy. The 4th slide is the only one that will contain a video and should be designed with that in mind. Attached to this contest, you will find two .pdf files. One contains a mockup of the new homepage containing dimensions and font requirements. The other is a spreadsheet containing copy for each slide.
In case you are unfamiliar with the brand, QuilNet® is the industry leader in online fax services. We provide faxing capabilities from mobile phones, tablets, and computers with state-of-the-art functionality, such as the ability to sign documents with your finger and send a document to any fax number directly from email.
Updates

FYI:  The dimensions of the video are 640x360.

Hello designers,

We don't want you to think we've forgotten about this contest.  We've been delayed in user testing but hope to have a response soon.

Thank you.

Target Market(s)

Mobile professionals and small businesses who need 24/7 access to fax services, such as lawyers, realtors, truckers, etc.

Industry/Entity Type

Industry

Requirements
Must have
• • The final deliverable should consist of a layered .psd file.
• Dimensions : 1500x475 (viewable area is 1200x475)
• Font is Google font – Lato
• Headline 62pt
• Subhead 32 pt

```html
<!DOCTYPE html>
<html lang="en">
<head>
<meta charset="utf-8">
<title>QuilNet® – Faxing Simplified</title>
<link href="https://fonts.googleapis.com/css2?family=Lato:ital,wght@0,300;0,400;0,700;0,900;1,400&display=swap" rel="stylesheet">
<style>
  :root {
    --ink: #222222;
    --navy: #0c3766;
    --red: #ff0a0a;
    --brand-red: #c8102e;
    --button-red: #a3080b;
    --nav-grey: #515151;
    --press-grey: #5a5a5a;
    --panel-grey: #efefef;
    --line: #d8d8d8;
    --white: #ffffff;
    --sky: #1aa9e6;
  }
  * { box-sizing: border-box; margin: 0; padding: 0; }
  html, body {
    width: 1200px; height: 640px; overflow: hidden;
    background: var(--white);
    font-family: "Lato", Arial, sans-serif;
    color: var(--ink);
  }
  .page { position: relative; width: 1200px; height: 640px; overflow: hidden; }

  .header { position: absolute; left: 122px; top: 0; width: 960px; height: 61px; }
  .brand { position: absolute; left: 12px; top: 14px; display: flex; align-items: center; gap: 7px; white-space: nowrap; }
  .brand-mark { width: 20px; height: 20px; border-radius: 50%; background: var(--brand-red); }
  .brand-name { font-size: 24px; font-weight: 900; color: var(--ink); letter-spacing: -0.4px; }
  .brand-tagline { margin-left: 6px; margin-top: 8px; font-size: 14px; font-style: italic; color: var(--ink); }

  .utility { position: absolute; top: 24px; display: flex; gap: 15px; left: 483px; font-size: 13.5px; font-weight: 700; white-space: nowrap; }
  .utility a { color: var(--ink); text-decoration: none; }
  .search {
    position: absolute; left: 646px; top: 23px; width: 106px; height: 20px;
    border: 1px solid var(--line); border-radius: 10px;
    font-size: 10px; font-style: italic; color: #aaaaaa; padding: 3px 10px;
  }
  .search svg { position: absolute; right: 7px; top: 3px; }
  .btn {
    position: absolute; top: 19px; height: 27px; border-radius: 4px;
    background: linear-gradient(#c0171a, var(--button-red));
    color: var(--white); font-size: 15px; font-weight: 700;
    display: flex; align-items: center; justify-content: center;
    box-shadow: 0 1px 2px rgba(0,0,0,.35);
  }
  .btn-signup { left: 772px; width: 80px; }
  .btn-login { left: 862px; width: 81px; }

  .main-nav {
    position: absolute; left: 122px; top: 61px; width: 960px; height: 39px;
    background: var(--nav-grey); color: var(--white);
    font-size: 18px; font-weight: 700;
  }
  .main-nav span { position: absolute; top: 9px; transform: translateX(-50%); white-space: nowrap; }

  .hero { position: absolute; left: 122px; top: 100px; width: 960px; height: 380px; overflow: hidden; }
  .hero-photo {
    position: absolute; inset: 0;
    background:
      radial-gradient(ellipse 340px 260px at 110px 200px, #ffffff 0%, rgba(255,255,255,0) 100%),
      linear-gradient(90deg, #e9eaec 0%, #dfe2e6 40%, #c9d1da 62%, #8fa6c4 80%, #b7c3d2 100%);
  }
  .hero-headline {
    position: absolute; left: 36px; top: 134px;
    font-size: 55px; font-weight: 700; line-height: 53px; letter-spacing: -0.3px;
  }
  .hero-headline .line-navy { color: var(--navy); display: block; }
  .hero-headline .line-red { color: var(--red); display: block; }

  .press { position: absolute; left: 122px; top: 480px; width: 960px; height: 77px; }
  .press-badge { position: absolute; top: 25px; height: 30px; background: var(--press-grey); border-radius: 3px; opacity: .85; }

  .feature {
    position: absolute; left: 122px; top: 557px; width: 960px; height: 83px;
    background: var(--panel-grey); overflow: hidden;
  }
  .feature-title {
    position: absolute; left: 19px; top: 46px;
    font-size: 36px; font-weight: 300; color: var(--navy); white-space: nowrap;
  }
  .feature-cloud {
    position: absolute; left: 668px; top: 24px; width: 230px; height: 120px;
    background: var(--sky); border-radius: 90px 90px 40px 40px;
    border: 3px solid var(--white);
  }
</style>
</head>
<body>
<div class="page">
  <header class="header">
    <div class="brand">
      <span class="brand-mark"></span>
      <span class="brand-name">QuilNet®</span>
      <span class="brand-tagline">Faxing Simplified</span>
    </div>
    <nav class="utility">
      <a href="#">Blog</a><a href="#">Help</a><a href="#">Contact Us</a>
    </nav>
    <div class="search">Search
      <svg width="12" height="12" viewBox="0 0 12 12"><circle cx="7" cy="5" r="3.5" fill="none" stroke="#999" stroke-width="1.3"/><line x1="4.5" y1="7.5" x2="1.5" y2="10.5" stroke="#999" stroke-width="1.5"/></svg>
    </div>
    <div class="btn btn-signup">Sign Up</div>
    <div class="btn btn-login">Login</div>
  </header>

  <nav class="main-nav">
    <span style="left:226px">Home</span>
    <span style="left:328px">Pricing</span>
    <span style="left:434px">Features</span>
    <span style="left:567px">How It Works</span>
    <span style="left:702px">About Us</span>
  </nav>

  <section class="hero">
    <div class="hero-photo" role="img" aria-label="Smiling professional typing on a laptop in a bright office with shelves of binders"></div>
    <h1 class="hero-headline">
      <span class="line-navy">FAXING WITHOUT A</span>
      <span class="line-red">FAX MACHINE</span>
    </h1>
  </section>

  <section class="press" aria-label="As featured in">
    <div class="press-badge" style="left:11px;width:153px"></div>
    <div class="press-badge" style="left:225px;width:121px"></div>
    <div class="press-badge" style="left:413px;width:118px"></div>
    <div class="press-badge" style="left:599px;width:188px"></div>
    <div class="press-badge" style="left:849px;width:97px"></div>
  </section>

  <section class="feature">
    <h2 class="feature-title">You mean I can fax by email?</h2>
    <div class="feature-cloud" role="img" aria-label="Blue cloud illustration representing sending faxes by email"></div>
  </section>
</div>
</body>
</html>
```